NexaBRIDGE new era @ Hyper Digitalization

We need a Brochure that show all our product, services and consulting related to Hyper Digitalization into the industrial internet of things world.
We need a document that can be handled as a electronic brochure, this means that we need to show strong corporate presence, with strong skill of technology, and we have credentials and key sucess projects related to Manufacturing industries.
Key industries that we attend: Automotive, Chemical, Food and Beverage, Mining, Paper and Pulp, Oil and Gas, Energy Management.
We save money to our customer in 6 ways: 1) Eficiency in operation 2) Production Control 3) Hyper Digitalization of Thing Optimizing asset ussage 4) Maintenance and predictive of assets risks 5) Quality Control reducing Cost 6) Augmented Reality in operation and control
Target Market(s)
Manufacturing Industry. CEO of companies that has challenges of saving operation costs into plants of manufacturing.
Industry/Entity Type
Software
Other font styles liked:
- MONTSERRAT
Requirements
Must have
- Technology Enviroment, our logo, our expertise, simple message about what our company does and the DNA, infography of the company, cases of sucess, cases of savings $ using our tecnology and services, what we can do for the customer in a few words
Nice to have
- standarize our colors related to our presentation, futuristic, information related to Artificial Inteligence related to machinery
Should not have
- old version of technology,

```html
<!DOCTYPE html>
<html lang="en">
<head>
<meta charset="utf-8">
<title>NexaBRIDGE – Hyper Digitalization Brochure Cover</title>
<link rel="stylesheet" href="https://fonts.googleapis.com/css2?family=Montserrat:wght@400;700&display=swap">
<style>
  :root {
    --backdrop: #e4dcd7;
    --photo-dark: #0d1510;
    --photo-green: #3f5a35;
    --photo-glow: #a8b47a;
    --band-light: #6f9fcf;
    --blue-deep: #1a5eab;
    --blue-soft: #4f86c0;
    --accent-green: #8cc63f;
    --tab-grey: #c9cbcc;
    --brand-blue: #2a8fd0;
    --title-ink: #1e2026;
    --motif-blue: #a9c6ea;
  }
  html, body {
    margin: 0;
    padding: 0;
    width: 1200px;
    height: 790px;
    overflow: hidden;
    background: var(--backdrop);
  }
  .canvas {
    position: relative;
    width: 1200px;
    height: 790px;
    font-family: "Montserrat", sans-serif;
  }
  .cover {
    position: absolute;
    left: 342px;
    top: 30px;
    width: 516px;
    height: 730px;
    overflow: hidden;
    box-shadow: 0 10px 28px rgba(60, 40, 30, 0.18);
  }
  .cover-art {
    position: absolute;
    inset: 0;
    width: 516px;
    height: 730px;
  }
  .brand-tab {
    position: absolute;
    left: 0;
    top: 0;
    width: 212px;
    height: 62px;
    background: var(--tab-grey);
    border-bottom-right-radius: 18px;
  }
  .brand-tab__rule {
    position: absolute;
    left: 22px;
    bottom: -3px;
    width: 128px;
    height: 3px;
    background: var(--accent-green);
  }
  .brand-name {
    position: absolute;
    left: 30px;
    top: 19px;
    margin: 0;
    font-weight: 400;
    font-size: 20px;
    letter-spacing: 0.5px;
    color: var(--brand-blue);
  }
  .cover-title {
    position: absolute;
    left: 0;
    top: 0;
    margin: 0;
    font-weight: 700;
    color: var(--title-ink);
    line-height: 1;
  }
  .cover-title__line {
    position: absolute;
    white-space: nowrap;
    font-size: 38px;
  }
  .cover-title__line--hyper {
    left: 176px;
    top: 492px;
  }
  .cover-title__line--digital {
    left: 200px;
    top: 540px;
  }
</style>
</head>
<body>
<main class="canvas">
  <article class="cover">
    <svg class="cover-art" viewBox="0 0 516 730" xmlns="http://www.w3.org/2000/svg">
      <defs>
        <radialGradient id="photoTone" cx="0.62" cy="0.38" r="0.7">
          <stop offset="0" stop-color="var(--photo-glow)"/>
          <stop offset="0.35" stop-color="var(--photo-green)"/>
          <stop offset="1" stop-color="var(--photo-dark)"/>
        </radialGradient>
        <linearGradient id="blueTone" x1="0" y1="0" x2="1" y2="0">
          <stop offset="0" stop-color="var(--blue-soft)"/>
          <stop offset="0.35" stop-color="var(--blue-deep)"/>
          <stop offset="0.75" stop-color="var(--blue-deep)"/>
          <stop offset="1" stop-color="var(--blue-soft)"/>
        </linearGradient>
        <linearGradient id="motifTone" x1="0" y1="0" x2="1" y2="0">
          <stop offset="0" stop-color="var(--motif-blue)" stop-opacity="0.55"/>
          <stop offset="1" stop-color="var(--motif-blue)" stop-opacity="0.15"/>
        </linearGradient>
      </defs>

      <rect class="cover-base" x="0" y="0" width="516" height="730" fill="url(#blueTone)"/>

      <polygon class="cover-band" points="0,270 245,462 516,240 516,285 245,480 0,312" fill="var(--band-light)"/>

      <polygon class="cover-photo" role="img"
               aria-label="Night photograph of futuristic glass skyscrapers with a green-lit sky"
               points="0,0 516,0 516,240 245,462 0,270" fill="url(#photoTone)"/>

      <line class="cover-tip-rule" x1="245" y1="481" x2="318" y2="429" stroke="var(--accent-green)" stroke-width="3"/>

      <rect class="network-motif" role="img"
            aria-label="Decorative chain of connected squares suggesting a digital network"
            x="22" y="548" width="166" height="56" rx="4" fill="url(#motifTone)"/>
    </svg>

    <header class="brand-tab">
      <p class="brand-name">NexaBRIDGE</p>
      <span class="brand-tab__rule"></span>
    </header>

    <h1 class="cover-title">
      <span class="cover-title__line cover-title__line--hyper">Hyper</span>
      <span class="cover-title__line cover-title__line--digital">Digitalization</span>
    </h1>
  </article>
</main>
</body>
</html>
```